Business Card Design for Software Development Company

I am looking for a business card design the incorporates my new logo (attached below).

Key information to include:
Name: Martin Quelbrook
Title: CEO
Email: martin@brightwellcivic.example
Phone: 555-218-9403
Website: www.brightwellcivic.example

NOTE: This design should be easy to edit so that we can order cards for different members of our team.

```html
<!DOCTYPE html>
<html lang="en">
<head>
<meta charset="utf-8">
<title>BrightwellLabs Business Card</title>
<link rel="stylesheet" href="https://fonts.googleapis.com/css2?family=Poppins:wght@400;500;600;700&display=swap">
<style>
  :root {
    --page: #161616;
    --card: #2f4a5d;
    --card-deep: #2a4356;
    --pattern-a: #3a5569;
    --pattern-b: #4a6479;
    --white: #ffffff;
    --teal: #19a88f;
    --orange: #f0702a;
    --red: #d6402f;
  }
  * { margin: 0; padding: 0; box-sizing: border-box; }
  html, body {
    width: 900px; height: 1200px; overflow: hidden;
    background: var(--page);
    font-family: "Poppins", sans-serif;
    color: var(--white);
  }
  .card {
    position: absolute;
    width: 630px; height: 360px;
    background: linear-gradient(160deg, var(--card) 0%, var(--card-deep) 100%);
    box-shadow: 0 10px 24px rgba(0,0,0,.45);
    overflow: hidden;
  }
  .card--front { left: 135px; top: 213px; }
  .card--back { left: 136px; top: 627px; }

  .card__pattern {
    position: absolute; inset: 0;
    background: linear-gradient(180deg, var(--pattern-a) 0%, var(--card) 50%, var(--pattern-a) 100%);
    opacity: .7;
  }
  .brand {
    position: absolute;
    display: flex; flex-direction: column; align-items: flex-end;
  }
  .brand__row { display: flex; align-items: center; gap: 12px; }
  .brand__dot { border-radius: 50%; background: var(--orange); flex: none; }
  .brand__name { font-weight: 600; line-height: 1; letter-spacing: -0.5px; color: var(--white); }
  .brand__tagline { font-weight: 600; text-transform: uppercase; letter-spacing: .3px; color: var(--white); }

  .card--front .brand { left: 65px; top: 140px; }
  .card--front .brand__dot { width: 42px; height: 42px; }
  .card--front .brand__name { font-size: 54px; }
  .card--front .brand__tagline { font-size: 8px; margin-top: 6px; }

  .card--back .brand { left: 52px; top: 158px; }
  .card--back .brand__dot { width: 20px; height: 20px; }
  .card--back .brand__row { gap: 7px; }
  .card--back .brand__name { font-size: 25px; letter-spacing: -0.3px; }
  .card--back .brand__tagline { font-size: 4px; margin-top: 3px; }

  .divider {
    position: absolute; left: 315px; top: 121px;
    width: 2px; height: 120px; background: var(--white);
  }
  .contact { position: absolute; left: 334px; top: 118px; }
  .contact__name {
    font-size: 23px; font-weight: 700; line-height: 1.1;
    background: linear-gradient(180deg, var(--teal) 0%, var(--teal) 50%, var(--orange) 100%);
    -webkit-background-clip: text; background-clip: text; color: transparent;
  }
  .contact__title { font-size: 13px; font-weight: 500; margin-top: 1px; }
  .contact__rule {
    width: 30px; height: 2px; margin-top: 3px;
    background: linear-gradient(90deg, var(--teal), var(--orange));
  }
  .contact__list { list-style: none; margin-top: 9px; }
  .contact__item {
    display: flex; align-items: center; gap: 6px;
    font-size: 15px; height: 25px;
  }
  .contact__item--phone { letter-spacing: 2.5px; }
  .contact__icon { width: 14px; height: 14px; flex: none; }
</style>
</head>
<body>

<section class="card card--front">
  <div class="card__pattern" role="img" aria-label="Faint repeating brand-mark pattern across the card background"></div>
  <div class="brand">
    <div class="brand__row">
      <span class="brand__dot"></span>
      <span class="brand__name">BrightwellLabs</span>
    </div>
    <span class="brand__tagline">A division of Brightwell Civic</span>
  </div>
</section>

<section class="card card--back">
  <div class="brand">
    <div class="brand__row">
      <span class="brand__dot"></span>
      <span class="brand__name">BrightwellLabs</span>
    </div>
    <span class="brand__tagline">A division of Brightwell Civic</span>
  </div>

  <div class="divider"></div>

  <div class="contact">
    <h1 class="contact__name">Martin Quelbrook</h1>
    <p class="contact__title">CEO</p>
    <div class="contact__rule"></div>
    <ul class="contact__list">
      <li class="contact__item contact__item--phone">
        <svg class="contact__icon" viewBox="0 0 24 24" aria-hidden="true"><path fill="#e8552c" d="M6.6 10.8a15 15 0 0 0 6.6 6.6l2.2-2.2c.3-.3.7-.4 1-.2 1.1.4 2.3.6 3.6.6.6 0 1 .4 1 1V20c0 .6-.4 1-1 1A17 17 0 0 1 3 4c0-.6.4-1 1-1h3.5c.6 0 1 .4 1 1 0 1.3.2 2.5.6 3.6.1.3 0 .7-.2 1z"/></svg>
        <span>555-218-9403</span>
      </li>
      <li class="contact__item">
        <svg class="contact__icon" viewBox="0 0 24 24" aria-hidden="true"><rect x="2" y="5" width="20" height="14" fill="#e8552c"/><path d="M2 5l10 8 10-8" fill="none" stroke="#19a88f" stroke-width="2"/></svg>
        <span>martin@brightwellcivic.example</span>
      </li>
      <li class="contact__item">
        <svg class="contact__icon" viewBox="0 0 24 24" aria-hidden="true"><circle cx="12" cy="12" r="9" fill="none" stroke="#d6402f" stroke-width="2"/><path d="M3 12h18M12 3c3 3 3 15 0 18M12 3c-3 3-3 15 0 18" fill="none" stroke="#19a88f" stroke-width="1.6"/></svg>
        <span>www.brightwellcivic.example</span>
      </li>
    </ul>
  </div>
</section>

</body>
</html>
```